UI/UX Re-Do for TallyNest - a free to use project management platform for desktop and mobile.

UI/UX Re-Do for TallyNest
TallyNest is a free to use project management platform for desktop and mobile.
We are looking for help with our UI/UX re-design.
As of now the platform is totally functional.
The problem is around flow and look. We want TN to become something that any one can use to manage and even socialize any project. A project can be something work related like organizing a team around a software build, marketing campaign, shared client file space, etc... In fact, most of our current members are using TN for just such work projects.
We also see a project as planning a wedding, organizing a group trip, a simple to-do list, organizing a kids sports team, and so on...
To become a platform that people will use in their work and personal life we first need to become more intuitive and friendly - while maintaining advanced functionality for more advanced needs.
We need help to beautify, streamline, and simplify - while keeping all the functions.
The quickest way to understand TN, and our current issues is this short video:
https://vidlumo.example/w/Qa7KdP2mXzR
For sure see this link for the entire most recent description AND images:
https://tallynestapp.example/?p=HumbZ4KcWrT
The best way to understand TN is to actually use it:
https://tallynestapp.example
Should you choose to take a run at improving TN here are the details:
Please focus your ideas for mobile, it's where we have the biggest issues.
Feel free to get outside the box.
Avoid swipe oriented designs.
Feel free to focus on ideas over polished outputs.
Use any tool you like, PS, hand drawing, written description if you think that works best.
(FYI - we use mostly use Orvane Slides docs internally)
Point is illustration of ideas over tool choice.
Feel free to:
Create something totally new
And/or riff on what we have now
And/or riff on the new design we are considering (see images below)
|||
If we go the direction of the images/designs below the idea is to give people options on how they see/experience TN.
Just below is what we are calling Ground View. This is a more basic and simple flow. Probably a default to keep new users feeling comfortable at the start.
<img src="https://i.picbarn.example/8wNtLQe.jpg" style="width: 100%;">
https://i.picbarn.example/8wNtLQe.jpg
|||
We are calling this optional view Sky View. It is more advanced and can show all project, goal(renamed 'milestones') at the same time. This is more of a paint job on the current design.
<img src="https://i.picbarn.example/vhRmJxd.jpg" style="width: 100%;">
https://i.picbarn.example/vhRmJxd.jpg
|||
If you're submitting please let us know if you can also do the PS files for dev.
Not required, but once we nail down the concepts we want someone to hone in the PS files.
As an optional bonus we will also be giving credit to you/your company in TN.
Let us know if you do or don't want that.
We are excited to see your work!!
<img src=" " style="width: 100%;">
Target Market(s)
Anyone who needs to organize any project, big or small. The key is to make a super friendly user experience for new users while retaining advanced functions.
Industry/Entity Type
Management
Number of Pages Required
2 page

```html
<!DOCTYPE html>
<html lang="en">
<head>
<meta charset="utf-8">
<title>TallyNest – Startup Starter Kit</title>
<link href="https://fonts.googleapis.com/css2?family=Montserrat:wght@400;500;600&display=swap" rel="stylesheet">
<style>
  :root{
    --ink:#111111;
    --text:#444444;
    --muted:#555555;
    --orange:#ff8a00;
    --blue:#1f6fb5;
    --link:#1a5fb4;
    --black:#000000;
    --topbar:#f3f3f3;
    --line:#d8d8d8;
    --white:#ffffff;
  }
  *{box-sizing:border-box;margin:0;padding:0}
  html,body{width:1200px;height:1188px;overflow:hidden;background:var(--white);font-family:"Montserrat",sans-serif;color:var(--ink)}
  .app{position:relative;width:1200px;height:1188px}

  .topbar{position:absolute;left:0;top:0;width:1200px;height:118px;background:var(--topbar);border-bottom:1px solid var(--line)}
  .brand{position:absolute;left:21px;top:37px;height:46px;display:flex;align-items:center;gap:12px}
  .brand-dot{width:40px;height:40px;border-radius:50%;background:var(--black)}
  .brand-name{font-size:26px;font-weight:500;color:var(--ink)}
  .search{position:absolute;left:629px;top:37px;width:452px;height:47px;border:1px solid #cfcfcf;border-radius:24px;background:var(--white);display:flex;align-items:center;padding:0 16px 0 13px;font-size:14px;color:#777}
  .search span{flex:1}
  .menu{position:absolute;left:1122px;top:51px;font-size:14px;color:var(--muted);display:flex;align-items:center;gap:6px}

  .sidebar{position:absolute;left:0;top:118px;width:321px;height:1070px;border-right:1px solid var(--line)}
  .nav-item{height:65px;display:flex;align-items:center;font-size:15.5px;white-space:nowrap}
  .nav-item svg{flex:none}
  .nav-dark{background:var(--black);color:var(--white);padding-left:28px;gap:16px;border-bottom:1px solid #333}
  .nav-active{background:var(--orange);color:var(--white);padding-left:22px;gap:20px;height:66px;font-size:15px}
  .nav-light{color:var(--muted);padding-left:22px;gap:20px;font-size:14.5px}
  .nav-group{padding-top:17px;padding-bottom:2px;border-top:1px solid var(--line)}

  .card{position:absolute;left:340px;top:146px;width:837px;height:802px;border:1px solid var(--line);background:var(--white)}
  .card h1{position:absolute;left:26px;top:30px;font-size:34px;font-weight:500;color:var(--black)}
  .intro{position:absolute;left:26px;top:96px;width:770px;font-size:15px;line-height:26px;color:var(--text)}
  .intro p+p{margin-top:26px}
  .template{position:absolute;left:25px;width:800px}
  .template .num{position:absolute;left:0;top:-22px;width:44px;height:44px;border:2px solid #e2e2e2;border-radius:50%;display:flex;align-items:center;justify-content:center;font-size:19px;font-weight:600;color:var(--blue)}
  .template h3{position:absolute;left:66px;top:-34px;font-size:15px;font-weight:600;color:var(--black);white-space:nowrap}
  .template a{position:absolute;left:67px;top:0;font-size:12px;color:var(--link);text-decoration:none;white-space:nowrap}
  .btn-more{position:absolute;left:26px;top:720px;width:186px;height:43px;border-radius:22px;background:var(--orange);color:var(--white);font-size:15.5px;font-weight:500;display:flex;align-items:center;justify-content:center}

  .composer{position:absolute;left:340px;top:989px;width:837px;height:118px;border:1px solid var(--line)}
  .composer .field{position:absolute;left:29px;top:31px;width:534px;height:56px;border:1px solid #cfcfcf;border-radius:28px;display:flex;align-items:center;padding-left:24px;font-size:15.5px;color:var(--ink)}
  .tools{position:absolute;left:598px;top:46px;display:flex;align-items:center;gap:13px}
  .tools span{width:26px;height:26px;display:flex;align-items:center;justify-content:center}
  .tools .chat{background:var(--blue);border-radius:50%}

  .footer{position:absolute;left:340px;top:1140px;width:837px;text-align:center;font-size:15.5px;color:var(--ink)}
</style>
</head>
<body>
<div class="app">
  <header class="topbar">
    <div class="brand"><span class="brand-dot"></span><span class="brand-name">TallyNest</span></div>
    <div class="search"><span>Search</span>
      <svg width="14" height="14" viewBox="0 0 14 14"><circle cx="6" cy="6" r="4.5" fill="none" stroke="#999" stroke-width="1.8"/><path d="M9.3 9.3l3.5 3.5" stroke="#999" stroke-width="1.8"/></svg>
    </div>
    <div class="menu">Menu
      <svg width="13" height="11" viewBox="0 0 13 11"><path d="M0 1.5h13M0 5.5h13M0 9.5h13" stroke="var(--blue)" stroke-width="2.2"/></svg>
    </div>
  </header>

  <nav class="sidebar">
    <div class="nav-item nav-dark">
      <svg width="24" height="24" viewBox="0 0 24 24"><circle cx="18" cy="5" r="4" fill="#2f8fd8"/><circle cx="6" cy="12" r="4" fill="#2f8fd8"/><circle cx="18" cy="19" r="4" fill="#2f8fd8"/><path d="M18 5L6 12l12 7" stroke="#2f8fd8" stroke-width="2" fill="none"/></svg>
      Current Shared Project</div>
    <div class="nav-item nav-active">
      <svg width="14" height="14" viewBox="0 0 14 14"><path d="M4 3.2A5 5 0 1 0 10 3.2" fill="none" stroke="#fff" stroke-width="2"/><path d="M7 0.5v6" stroke="#fff" stroke-width="2"/></svg>
      Startup Starter Kit</div>
    <div class="nav-group">
      <div class="nav-item nav-light"><svg width="14" height="14" viewBox="0 0 14 14"><circle cx="7" cy="7" r="5.5" fill="none" stroke="#555" stroke-width="2"/><path d="M7 4v3.5h-2.5" stroke="#555" stroke-width="1.6" fill="none"/></svg>Meeting Notes/ Business SCRUM</div>
      <div class="nav-item nav-light"><svg width="14" height="14" viewBox="0 0 14 14"><rect x="2.5" y="0.5" width="9" height="13" fill="#555"/><path d="M4.5 3h1.5M8 3h1.5M4.5 6h1.5M8 6h1.5M4.5 9h1.5M8 9h1.5" stroke="#fff" stroke-width="1.2"/></svg>Corporate Structure</div>
      <div class="nav-item nav-light"><svg width="17" height="14" viewBox="0 0 17 14"><rect x="1" y="3" width="15" height="9" fill="none" stroke="#555" stroke-width="1.8"/><circle cx="8.5" cy="7.5" r="2.3" fill="#555"/></svg>Fund Raising / Corp Dev</div>
      <div class="nav-item nav-light"><svg width="15" height="14" viewBox="0 0 15 14"><rect x="1" y="4" width="13" height="9" rx="1.5" fill="#555"/><rect x="5" y="1.5" width="5" height="3" fill="none" stroke="#555" stroke-width="1.5"/></svg>Operating Finance</div>
      <div class="nav-item nav-light"><svg width="17" height="14" viewBox="0 0 17 14"><path d="M1 1v12h15" stroke="#555" stroke-width="1.6" fill="none"/><path d="M5 11V7M8 11V4M11 11V6M14 11V3" stroke="#555" stroke-width="2"/></svg>Sales /Business Development</div>
      <div class="nav-item nav-light"><svg width="17" height="14" viewBox="0 0 17 14"><path d="M1 1v12h15" stroke="#555" stroke-width="1.6" fill="none"/><path d="M3.5 10l4-4 3 3 5-6" stroke="#555" stroke-width="1.8" fill="none"/></svg>Marketing</div>
      <div class="nav-item nav-light"><svg width="15" height="14" viewBox="0 0 15 14"><path d="M14 0.5L0.5 6.5l4.5 1.8L12 2.5 6.3 9v4.3l2.5-3.2 3.5 2z" fill="#555"/></svg>Other</div>
    </div>
    <div class="nav-item nav-dark"><svg width="24" height="26" viewBox="0 0 24 26"><path d="M3 1h12l6 6v18H3z" fill="none" stroke="#2f8fd8" stroke-width="2"/><path d="M15 1v6h6M7 13h10M7 17h10M7 21h10" stroke="#2f8fd8" stroke-width="1.8" fill="none"/></svg>TallyNest Top Project Picks</div>
    <div class="nav-item nav-dark"><svg width="24" height="24" viewBox="0 0 24 24"><path d="M7 2h15l-4 20H3z" fill="#2f8fd8"/><path d="M9 7h9M8 11h9" stroke="#000" stroke-width="1.5"/></svg>Most Popular Public Projects</div>
    <div class="nav-item nav-dark"><svg width="26" height="24" viewBox="0 0 26 24"><circle cx="13" cy="7" r="4.5" fill="#2f8fd8"/><circle cx="5" cy="8" r="3.2" fill="#2f8fd8"/><circle cx="21" cy="8" r="3.2" fill="#2f8fd8"/><path d="M5 23v-5a8 8 0 0 1 16 0v5z" fill="#2f8fd8"/><path d="M0 19v-3a5 5 0 0 1 6-4.5L4 19zM26 19v-3a5 5 0 0 0-6-4.5L22 19z" fill="#2f8fd8"/></svg>All Public Projects</div>
  </nav>

  <main class="card">
    <h1>Welcome to Startup Starter Kit</h1>
    <div class="intro">
      <p>Sed ut perspiciatis unde omnis iste natus error sit voluptatem accusantium doloremque laudantium, totam rem aperiam, eaque ipsa quae ab illo inventore veritatis et quasi architecto beatae vitae dicta sunt explicabo. Nemo enim ipsam voluptatem quia voluptas sit aspernatur aut odit aut fugit, sed quia consequuntur magni.</p>
      <p>dolores eos qui ratione voluptatem sequi nesciunt. Neque porro quisquam est, qui dolorem ipsum quia dolor sit amet, consectetur, adipisci velit, sed quia non numquam eius modi tempora incidunt ut labore et dolore magnam aliquam quaerat voluptatem.</p>
    </div>

    <div class="template" style="top:371px"><div class="num">1</div><h3>TMP - General Business Scrum Template</h3><a href="#">https://docs.orvane.example/document/d/1xVXJPiTakOMzbHq380Mn1g4W7yq84n3UdiU1MJYhdwY/edit</a></div>
    <div class="template" style="top:468px"><div class="num">2</div><h3>TMP - Business Plan / Pitch Deck Research Template</h3><a href="#" style="left:70px">https://docs.orvane.example/presentation/d/10yJn5uLrVU5ng3AYXGNZAmbeJgkk1iBh6kb0nAr7eew/edit#slide=id.g1d83</a></div>
    <div class="template" style="top:559px"><div class="num">3</div><h3>TMP - Competitive Landscape Template</h3><a href="#" style="left:70px">https://docs.orvane.example/spreadsheets/d/16bwjSD624EP8_NFTSHoyfbmekenD1A2wY-o55OUyp4U/edit#gid=0</a></div>
    <div class="template" style="top:656px"><div class="num">4</div><h3>TPM - Revenue and Cost Model Compression TEMPLATE</h3><a href="#" style="left:70px">https://docs.orvane.example/spreadsheets/d/11f4pogNkbrD3fYIFTqf7FJat0a3a9taaAWweU2jCAQk/edit#gid=1268860158</a></div>

    <div class="btn-more">View More</div>
  </main>

  <section class="composer">
    <div class="field">Type Here</div>
    <div class="tools">
      <span class="chat"><svg width="16" height="15" viewBox="0 0 16 15"><ellipse cx="8" cy="6.5" rx="6.5" ry="5" fill="none" stroke="#fff" stroke-width="1.6"/><path d="M3.5 10l-1.5 4 4-2.5" fill="#fff"/></svg></span>
      <span><svg width="16" height="16" viewBox="0 0 16 16"><path d="M6.5 9.5l3-3" stroke="#111" stroke-width="1.8"/><path d="M7 4.5l1.5-1.5a2.5 2.5 0 0 1 3.5 3.5L10.5 8" fill="none" stroke="#111" stroke-width="2"/><path d="M9 11.5L7.5 13A2.5 2.5 0 0 1 4 9.5L5.5 8" fill="none" stroke="#111" stroke-width="2"/></svg></span>
      <span><svg width="17" height="14" viewBox="0 0 17 14"><rect x="0.5" y="3" width="16" height="10.5" rx="1.5" fill="#111"/><path d="M5 3l1.5-2.5h4L12 3z" fill="#111"/><circle cx="8.5" cy="8.2" r="3" fill="#fff"/><circle cx="8.5" cy="8.2" r="1.7" fill="#111"/></svg></span>
      <span><svg width="16" height="16" viewBox="0 0 16 16"><rect x="5" y="1" width="10" height="10" fill="none" stroke="#111" stroke-width="1.8"/><rect x="1" y="5" width="10" height="10" fill="#fff" stroke="#111" stroke-width="1.8"/></svg></span>
    </div>
  </section>

  <footer class="footer">© 2017 Company Name &nbsp;|&nbsp; All Rights &nbsp;Reserved</footer>
</div>
</body>
</html>
```